Ledger Lanternfox Powerpoint with Marshal Valorline Type Theme

Need powerpoint template with matching colors and different slide options. Logo and colors to be used can be found at ledgerlanternfox.example. Want brightly colored slide deck that is readable form the back of a room, but highlights colors. I will be incorporating Quizzap into the slides to gamify my presentations.

Target Market(s)

Tech

Industry/Entity Type

IT, specifically database, but crossing over to mental health in IT, important note this is not for a company, this is just for a professional building a brand

Font styles to use
Sans Serif

Colors
0054AA
0677BA
7BADD7
CADEEF
E8F1F8
EB3D1F
EC4F4E
F09395
F8D3D4
FCEDEE

Requirements
Must have
• My Logo in the bottom corner, front page, a thank your page, question page, content page, content page with two columns, content page with graphs, and icons to be used in the primary colors of the logos, About Me Page, Break Slides, Demo break slide
Should not have
• Lighter shades of colors, I want to pop out where colors are used, I want spacing and font size to be readable from the back of a room, most likely black text and white background

```html
<!DOCTYPE html>
<html lang="en">
<head>
<meta charset="utf-8">
<title>About Me – Marla Quintrell</title>
<link rel="stylesheet" href="https://fonts.googleapis.com/css2?family=Roboto:wght@400;700;900&display=swap">
<style>
  :root {
    --navy: #173f73;
    --banner: #86b3dc;
    --banner-fold: #6a96bf;
    --white: #ffffff;
    --brand-red: #eb3d1f;
    --footer-grey: #c9ced6;
  }
  * { margin: 0; padding: 0; box-sizing: border-box; }
  html, body { width: 1200px; height: 675px; overflow: hidden; background: var(--white); }
  .slide {
    position: relative;
    width: 1200px;
    height: 675px;
    overflow: hidden;
    background: var(--white);
    font-family: "Roboto", Arial, sans-serif;
  }
  .slide-shapes { position: absolute; inset: 0; }
  .banner-fill { fill: var(--banner); }
  .banner-fold { fill: var(--banner-fold); }
  .ring { fill: var(--navy); }
  .bio {
    position: absolute;
    left: 360px;
    top: 240px;
    width: 720px;
    color: var(--white);
  }
  .bio-name {
    font-size: 34px;
    font-weight: 700;
    letter-spacing: 0.3px;
    line-height: 1.2;
    margin-bottom: 20px;
  }
  .bio-text {
    font-size: 18.6px;
    font-weight: 400;
    line-height: 35.6px;
  }
  .footer-company {
    position: absolute;
    left: 90px;
    top: 651px;
    font-size: 10px;
    color: var(--footer-grey);
  }
  .brand-mark {
    position: absolute;
    right: 69px;
    bottom: 24px;
    width: 200px;
    font-size: 24px;
    font-weight: 900;
    color: var(--brand-red);
    letter-spacing: 0.2px;
    text-transform: uppercase;
    line-height: 1;
    text-align: right;
  }
</style>
</head>
<body>
  <main class="slide">
    <svg class="slide-shapes" width="1200" height="675" viewBox="0 0 1200 675" aria-hidden="true">
      <polygon class="banner-fill" points="256,129 1131,129 1131,494 1072,550 256,550"/>
      <polygon class="banner-fold" points="1072,550 1131,494 1084,506"/>
      <path class="ring" fill-rule="evenodd"
            d="M -335 340 A 335 335 0 1 0 335 340 A 335 335 0 1 0 -335 340 Z
               M -130 340 A 130 130 0 1 0 130 340 A 130 130 0 1 0 -130 340 Z"/>
    </svg>

    <section class="bio">
      <h1 class="bio-name">MARLA QUINTRELL</h1>
      <p class="bio-text">Marla Quintrell is currently a Data Platform Champion, DataHeart 2020 Award winner, and works as a Senior Database Administrator for SignHarbor. Marla has worked on QueryBase since 4.2. She is currently a co-leader of the Harborview QueryBase User Group in Larkfield, OR and the Inclusive Data Circle. Marla first built databases as a teenager to catalog her vintage stamp collection and never looked back.</p>
    </section>

    <p class="footer-company">Company Name Here</p>
    <p class="brand-mark">Ledger Lanternfox</p>
  </main>
</body>
</html>
```